Modern labels for Vorquin products

We need a new design of our labels for the product “Vorquin” (https://www.vorquin.eu/#) . The reason why we want to change our labels is to get a modern and more advanced look of our product. We also want to create a unique product that is attractive for our customers, even if the product are used in hospitals and healthcare centers for collecting dangerous waste.

There is three sizes of labels (55x95, 90x95, 170x95 mm) for different boxes, but the label will contain similar information. There are certain requirements and factors from regulations/standards that you need to follow when you create the new layout. But it’s up to you to change the design. You can work with background, fonts, effects, colors, structure, pattern, new symbols, logotype etc. The label could be any color, but the container will stay yellow so they have to look good together.

Keywords: Elegant, modern, functional, attractive, exclusive

Target Market(s)

Hospitals and healthcare centers

Industry/Entity Type

Product

Font styles to use
Serif
Sans Serif

Colors

Designer to choose colors to be used in the design.

Requirements
Must have
• Requirements for the regulations ADR UN3291 and ISO 23907 (PDF).
• * Symbol for danger waste
• * Filling level
• * "Danger"
• * Symbol for no second use
• * Symbol for manufaturer
• * Referencenumber
• * Text "”Clinical waste, Unspecified, N.O.S.”"
• * Area for series, certification, size and useful capacity
• * Area for Illustrations.
• * Text “Autoclavable at 134 c”, “Do not force closure” and “Do not overfill”.
• * Text for certification ”UN 3291 1H2/Y0,3/S/YR/N/NET2903A”
• Three different sizes (55x95, 90x95, 170x95).
• More info in PDF "3kravspecifikation"
Nice to have
• A modern, elegant, advanced look of our label.
Should not have
• The information must be clear and readable, not too decorative/handwriting fonts.

```html
<!DOCTYPE html>
<html lang="en">
<head>
<meta charset="utf-8">
<title>Vorquin sharps container labels</title>
<link href="https://fonts.googleapis.com/css2?family=Oswald:wght@500;700&family=Roboto+Condensed:wght@400;700&family=Bitter:wght@800&display=swap" rel="stylesheet">
<style>
:root{
  --yellow:#fccb05;
  --red:#f40009;
  --black:#111;
  --white:#fff;
  --cell:#e6e6e6;
  --brand-red:#8a0006;
}
html,body{margin:0;padding:0;width:1000px;height:1200px;overflow:hidden;background:var(--white);}
.sheet{position:relative;width:1250px;height:1500px;transform:scale(.8);transform-origin:0 0;font-family:"Roboto Condensed",Arial,sans-serif;color:var(--black);}
.shapes{position:absolute;left:0;top:0;}
.t{position:absolute;white-space:nowrap;line-height:1;}
.fill-level{font-family:"Oswald",sans-serif;font-weight:700;color:var(--yellow);text-align:center;display:flex;align-items:center;justify-content:center;}
.waste-title{font-family:"Oswald",sans-serif;font-weight:700;color:var(--white);}
.danger{font-family:"Oswald",sans-serif;font-weight:700;color:var(--red);text-align:center;}
.substance{font-family:"Bitter",serif;font-weight:800;text-align:center;color:var(--black);}
.notify{text-align:center;line-height:1.2;}
.class-six{font-family:"Oswald",sans-serif;font-weight:700;text-align:center;}
.no-use{font-family:"Oswald",sans-serif;font-weight:700;text-align:right;}
.no-use b{display:block;}
.on-red{color:var(--white);}
.on-white{color:var(--red);}
.brand{font-family:"Roboto Condensed",sans-serif;font-weight:700;color:var(--black);}
.brand-small{font-family:"Roboto Condensed",sans-serif;font-weight:700;color:var(--white);}
.maker-line{color:var(--brand-red);line-height:1.3;}
.un-number{font-family:"Roboto Condensed",sans-serif;font-weight:700;}
.un-code{font-family:"Roboto Condensed",sans-serif;letter-spacing:-.3px;}
.info-box{position:absolute;background:var(--white);border:2px solid var(--black);border-radius:5px;box-sizing:border-box;display:flex;flex-direction:column;justify-content:space-around;padding:0 6px;}
.info-box .row{display:flex;justify-content:space-between;white-space:nowrap;gap:4px;}
.info-box em{font-weight:700;}
.form-box{position:absolute;background:var(--white);border:2px solid var(--black);border-radius:5px;box-sizing:border-box;display:flex;flex-direction:column;}
.form-box span{flex:1;display:flex;align-items:center;padding-left:4px;border-bottom:1.5px solid var(--black);}
.form-box span:last-child{border-bottom:none;}
.step{position:absolute;font-family:"Roboto Condensed",sans-serif;}
.vertical{transform-origin:0 0;transform:rotate(-90deg);}
</style>
</head>
<body>
<div class="sheet">

<svg class="shapes" width="1250" height="1500" viewBox="0 0 1250 1500" xmlns="http://www.w3.org/2000/svg">
  <rect x="68" y="66" width="1112" height="620" rx="38" fill="var(--yellow)"/>
  <path d="M126 106 H873 V652 H126 Q108 652 108 634 V124 Q108 106 126 106 Z" fill="var(--red)"/>
  <polygon points="1140,415 1140,652 905,652" fill="var(--red)"/>
  <polygon points="873,108 1138,380 873,650 608,380" fill="var(--white)"/>
  <polygon points="873,136 1111,380 873,623 635,380" fill="none" stroke="var(--black)" stroke-width="4"/>
  <g role="img" aria-label="Biohazard warning symbol"><circle cx="873" cy="280" r="82" fill="var(--black)"/></g>
  <polygon points="146,141 178,119 178,128 700,128 700,119 732,141 700,163 700,154 178,154 178,163" fill="var(--black)"/>
  <rect x="148" y="228" width="336" height="248" rx="6" fill="var(--white)" stroke="var(--black)" stroke-width="3"/>
  <rect x="175" y="236" width="118" height="88" fill="var(--cell)" role="img" aria-label="Step 1: open container"/>
  <rect x="325" y="236" width="152" height="88" fill="var(--cell)" role="img" aria-label="Step 3: disposing sharps"/>
  <rect x="175" y="338" width="118" height="130" fill="var(--cell)" role="img" aria-label="Step 2: clicking lid closed"/>
  <rect x="306" y="338" width="171" height="130" fill="var(--cell)" role="img" aria-label="Temporary and final closure"/>
  <line x1="298" y1="228" x2="298" y2="476" stroke="var(--black)" stroke-width="2.5"/>
  <line x1="148" y1="330" x2="484" y2="330" stroke="var(--black)" stroke-width="2.5"/>
  <polygon points="147,618 147,588 160,598 160,588 173,598 173,588 186,598 186,580 198,580 198,618" fill="var(--black)"/>

  <path d="M88 737 H448 Q468 737 468 757 V1428 H68 V757 Q68 737 88 737 Z" fill="var(--yellow)"/>
  <path d="M92 930 H444 Q452 930 452 938 V1428 H84 V938 Q84 930 92 930 Z" fill="var(--red)"/>
  <polygon points="432,940 432,1083 292,1083" fill="var(--white)"/>
  <polygon points="268,793 400,925 268,1058 136,925" fill="var(--white)"/>
  <polygon points="268,808 385,925 268,1043 151,925" fill="none" stroke="var(--black)" stroke-width="3"/>
  <g role="img" aria-label="Biohazard warning symbol"><circle cx="268" cy="876" r="40" fill="var(--black)"/></g>
  <polygon points="84,766 106,751 106,758 430,758 430,751 452,766 430,781 430,774 106,774 106,781" fill="var(--black)"/>
  <rect x="140" y="1098" width="292" height="217" rx="5" fill="var(--white)" stroke="var(--black)" stroke-width="3"/>
  <rect x="160" y="1104" width="106" height="78" fill="var(--cell)" role="img" aria-label="Step 1: open container"/>
  <rect x="294" y="1104" width="132" height="78" fill="var(--cell)" role="img" aria-label="Step 3: disposing sharps"/>
  <rect x="160" y="1193" width="106" height="116" fill="var(--cell)" role="img" aria-label="Step 2: clicking lid closed"/>
  <rect x="277" y="1193" width="149" height="116" fill="var(--cell)" role="img" aria-label="Temporary and final closure"/>
  <line x1="271" y1="1098" x2="271" y2="1315" stroke="var(--black)" stroke-width="2"/>
  <line x1="140" y1="1187" x2="432" y2="1187" stroke="var(--black)" stroke-width="2"/>
  <polygon points="138,1410 138,1388 147,1395 147,1388 156,1395 156,1388 165,1395 165,1380 175,1380 175,1410" fill="var(--black)"/>

  <path d="M547 737 H1153 Q1178 737 1178 762 V1403 Q1178 1428 1153 1428 H547 Q522 1428 522 1403 V762 Q522 737 547 737 Z" fill="var(--yellow)"/>
  <path d="M560 1002 H1138 Q1150 1002 1150 1014 V1428 H548 V1014 Q548 1002 560 1002 Z" fill="var(--red)"/>
  <polygon points="1133,1018 1133,1197 958,1197" fill="var(--white)"/>
  <polygon points="850,805 1040,1000 850,1195 660,1000" fill="var(--white)"/>
  <polygon points="850,826 1019,1000 850,1174 681,1000" fill="none" stroke="var(--black)" stroke-width="3.5"/>
  <g role="img" aria-label="Biohazard warning symbol"><circle cx="850" cy="928" r="58" fill="var(--black)"/></g>
  <polygon points="548,779 576,759 576,767 1122,767 1122,759 1150,779 1122,799 1122,791 576,791 576,799" fill="var(--black)"/>
  <rect x="568" y="1213" width="274" height="203" rx="5" fill="var(--white)" stroke="var(--black)" stroke-width="3"/>
  <rect x="588" y="1219" width="98" height="73" fill="var(--cell)" role="img" aria-label="Step 1: open container"/>
  <rect x="714" y="1219" width="122" height="73" fill="var(--cell)" role="img" aria-label="Step 3: disposing sharps"/>
  <rect x="588" y="1304" width="98" height="106" fill="var(--cell)" role="img" aria-label="Step 2: clicking lid closed"/>
  <rect x="697" y="1304" width="139" height="106" fill="var(--cell)" role="img" aria-label="Temporary and final closure"/>
  <line x1="691" y1="1213" x2="691" y2="1416" stroke="var(--black)" stroke-width="2"/>
  <line x1="568" y1="1298" x2="842" y2="1298" stroke="var(--black)" stroke-width="2"/>
  <polygon points="863,1405 863,1384 872,1391 872,1384 881,1391 881,1384 890,1391 890,1376 900,1376 900,1405" fill="var(--black)"/>
</svg>

<div class="t fill-level" style="left:146px;top:128px;width:586px;height:26px;font-size:24px;letter-spacing:14px;">FILLING LEVEL</div>
<div class="t waste-title" style="left:148px;top:166px;font-size:43px;">Clinical Waste, Unspecified, N.O.S.</div>
<div class="t brand" style="left:920px;top:102px;font-size:46px;">Vorquin</div>
<div class="step" style="left:156px;top:242px;font-size:18px;">1</div>
<div class="step" style="left:306px;top:240px;font-size:18px;">3</div>
<div class="step" style="left:152px;top:350px;font-size:18px;">2</div>
<div class="info-box" style="left:148px;top:488px;width:478px;height:57px;font-size:15.5px;">
  <div class="row" style="padding:0 14px;"><span>Autoclavable at 134 C</span><span>•</span><span>Do not force closure</span><span>•</span><span>Do not overfill</span></div>
  <div class="row"><span>Series: <em>Nova</em> Certification: <em>ISO 23907:2012</em></span><span>Size: <em>2,2 L</em></span><span>Usefulcapcity: 1,76 L</span></div>
</div>
<div class="t brand-small" style="left:212px;top:566px;font-size:26px;">Vorquin</div>
<div class="t maker-line" style="left:212px;top:594px;font-size:11px;">Lundholm, Sweden<br>www.vorquin.eu</div>
<div class="form-box" style="left:365px;top:557px;width:261px;height:73px;font-size:11.5px;"><span>Etablissement</span><span>Unité de soins</span><span>Mise en service</span></div>
<div class="t danger" style="left:723px;top:366px;width:300px;font-size:56px;">DANGER</div>
<div class="t substance" style="left:673px;top:430px;width:400px;font-size:25px;">INFECTIONS SUBSTANCE</div>
<div class="t notify" style="left:723px;top:463px;width:300px;font-size:20px;">In Case Of Damage Or Leakage<br>Immediately Notify Public<br>Health Authority</div>
<div class="t class-six" style="left:823px;top:538px;width:100px;font-size:60px;">6</div>
<div class="t no-use on-red" style="left:930px;top:530px;width:200px;"><b style="font-size:76px;">NO</b><b style="font-size:32px;margin-top:4px;">SECOND USE</b></div>

<div class="t fill-level" style="left:84px;top:758px;width:368px;height:16px;font-size:14px;letter-spacing:8px;">FILLING LEVEL</div>
<div class="t brand" style="left:84px;top:789px;font-size:30px;">Vorquin</div>
<div class="t un-number" style="left:332px;top:784px;font-size:32px;">UN3291</div>
<div class="t un-code" style="left:334px;top:817px;font-size:10px;">◯ 1H2/Y0.7/S/YR/N/VQN1187A</div>
<div class="t danger" style="left:168px;top:921px;width:200px;font-size:29px;">DANGER</div>
<div class="t substance" style="left:168px;top:954px;width:200px;font-size:12px;">INFECTIONS SUBSTANCE</div>
<div class="t notify" style="left:168px;top:971px;width:200px;font-size:9.5px;">In Case Of Damage Or Leakage<br>Immediately Notify Public<br>Health Authority</div>
<div class="t class-six" style="left:238px;top:1008px;width:60px;font-size:34px;">6</div>
<div class="t no-use on-white" style="left:232px;top:1012px;width:196px;"><b style="font-size:46px;">NO</b><b style="font-size:20px;margin-top:2px;">SECOND USE</b></div>
<div class="t waste-title vertical" style="left:92px;top:1418px;font-size:31px;">Clinical Waste, Unspecified, N.O.S.</div>
<div class="step" style="left:146px;top:1110px;font-size:15px;">1</div>
<div class="step" style="left:278px;top:1110px;font-size:15px;">3</div>
<div class="step" style="left:144px;top:1207px;font-size:15px;">2</div>
<div class="info-box" style="left:140px;top:1330px;width:292px;height:33px;font-size:9px;padding:0 4px;">
  <div class="row" style="padding:0 6px;"><span>Autoclavable at 134 C</span><span>•</span><span>Do not force closure</span><span>•</span><span>Do not overfill</span></div>
  <div class="row"><span>Series: <em>Nova</em> Certification: <em>ISO 23907:2012</em></span><span>Size: <em>2,2 L</em></span><span>Usefulcapcity: 1,76 L</span></div>
</div>
<div class="t brand-small" style="left:185px;top:1372px;font-size:19px;">Vorquin</div>
<div class="t maker-line" style="left:185px;top:1393px;font-size:8px;">Lundholm, Sweden<br>www.vorquin.eu</div>
<div class="form-box" style="left:282px;top:1370px;width:150px;height:44px;font-size:7.5px;"><span>Etablissement</span><span>Unité de soins</span><span>Mise en service</span></div>

<div class="t fill-level" style="left:548px;top:767px;width:602px;height:24px;font-size:22px;letter-spacing:16px;">FILLING LEVEL</div>
<div class="t brand" style="left:548px;top:812px;font-size:48px;">Vorquin</div>
<div class="t un-number" style="left:950px;top:808px;font-size:56px;">UN3291</div>
<div class="t un-code" style="left:952px;top:864px;font-size:17px;">◯ 1H2/Y0.7/S/YR/N/VQN1187A</div>
<div class="t danger" style="left:725px;top:992px;width:250px;font-size:41px;">DANGER</div>
<div class="t substance" style="left:700px;top:1037px;width:300px;font-size:18px;">INFECTIONS SUBSTANCE</div>
<div class="t notify" style="left:725px;top:1062px;width:250px;font-size:14px;">In Case Of Damage Or Leakage<br>Immediately Notify Public<br>Health Authority</div>
<div class="t class-six" style="left:820px;top:1114px;width:60px;font-size:46px;">6</div>
<div class="t no-use on-white" style="left:930px;top:1104px;width:198px;"><b style="font-size:58px;">NO</b><b style="font-size:25px;margin-top:3px;">SECOND USE</b></div>
<div class="t waste-title" style="left:560px;top:1106px;font-size:39px;line-height:1.3;">Clinical Waste,<br>Unspecified, N.O.S.</div>
<div class="step" style="left:574px;top:1225px;font-size:14px;">1</div>
<div class="step" style="left:698px;top:1224px;font-size:14px;">3</div>
<div class="step" style="left:572px;top:1314px;font-size:14px;">2</div>
<div class="info-box" style="left:863px;top:1215px;width:270px;height:50px;font-size:8.2px;padding:0 4px;">
  <div class="row" style="padding:0 6px;"><span>Autoclavable at 134 C</span><span>•</span><span>Do not force closure</span><span>•</span><span>Do not overfill</span></div>
  <div class="row"><span>Series: <em>Nova</em> Certification: <em>ISO 23907:2012</em></span><span>Size: <em>2,2 L</em></span><span>Usefulcapcity: 1,76 L</span></div>
</div>
<div class="form-box" style="left:863px;top:1275px;width:270px;height:77px;font-size:12px;"><span>Etablissement</span><span>Unité de soins</span><span>Mise en service</span></div>
<div class="t brand-small" style="left:910px;top:1367px;font-size:20px;">Vorquin</div>
<div class="t maker-line" style="left:910px;top:1389px;font-size:8px;">Lundholm, Sweden<br>www.vorquin.eu</div>

</div>
</body>
</html>
```